Women's Jewellery startup needs a captivating, beautifully designed and intuitive online store

[12/24 update]

Added 2 additional documents:

Feedback on designs received so far: designer feedback.docx
Product images from catalogue: products images.docx

Please read the feedback provided on designs provided so far to guide you further on your submission. The product images can be used to create promotional banners for the site.

@@@Added a document (VELISTO JEWELLERY_checklist.docx) which can be used by designers as a checklist when submitting their designs to ensure all aspects of the requirements have been covered @@@

+++IMPORTANT BUT NOT SPECIFIED IN THE REQUIREMENTS DOCUMENT - DESIGN SHOULD INCLUDE SUPPORT FOR MOBILE FRIENDLY SITE TOO+++

***Previous experience designing Jewellery online stores preferred (not essential)***

The name of the online Jewellery store is "Velisto Jewellery" and the business is based in Hong Kong. It will be run by 2 stay at home mothers. We need a Shopify themed store designed that will achieve the following objectives in order of priority:

• Conversion: The primary objective of the design/content is to prompt the customer to make a purchase. While this may sound obvious, it is mentioned so as not to distract the design process by focusing on other objectives (which are also important). The site also needs to be optimized so as to rank high in search engine searches for relevant keywords (SEO)
• Navigation: An intuitive interface which takes away a lot of the thinking from the customer by making it obvious what they need to do when they visit the store
• Engagement: Encourages the customer to spend time on the website and share content with their social network

Where applicable, the design of the store should reflect as closely as possible the mission statements and words outlined below:

• Jewellery you’ll fall in love with
• We want every client to leave the store with a smile
• We want to be able to provide the best service we can in every situation no matter what
• We aim to increase our business by word of mouth; therefore we tell people things about our store that makes it interesting for them to share
• We love every customer, no matter how difficult things get
• We, as a team, are so well informed about our products and brands that we always have the best information for our customers
• We celebrate women here!
• We celebrate life in here!
• We celebrate beauty here!
• We celebrate families here, as jewellery often stays within families.
• We will always try to make an extra step
• We will always try to exceed the expectation of our customers
• We will go as far as we possibly can to attract a customer back to our store and connect with us
• Every client that leaves our store knows more about jewellery because we passionately told him about it
• Romantic, classic, love, warm, cool, stylish

A draft functional specification is attached with this brief. We would like the design to reflect as closely as possible the functional requirements outlined in the document. Open to suggestions to improve upon the functional requirements.

Target Market(s)

Women aged 18-55

Industry/Entity Type

Jewelry Store

Coding

Coded - Design and coding required

Number of Pages Required

5+ page

Font styles to use
Other font styles liked:
• Myriad Pro as per Logo but open to any font that complements this one

Requirements
Must have
• 1. A look that encourages the user to make a purchase
• 2. An intuitive, easy to navigate and engaging interface
• 3. Primary colour scheme as defined in the functional specification attached
• 4. Simplistic look, not too cluttered
Nice to have
• 1. Closely matching the functional requirements of the site as outlined in the requirements specification but open to any better ideas

```html
<!DOCTYPE html>
<html lang="en">
<head>
<meta charset="utf-8">
<title>Velisto Jewellery</title>
<link href="https://fonts.googleapis.com/css2?family=Source+Sans+3:wght@400;600;700&display=swap" rel="stylesheet">
<style>
:root{
  --gold:#c8913a;
  --gold-dark:#6b4a1a;
  --ink:#333333;
  --text:#555555;
  --muted:#888888;
  --page:#f2f2f2;
  --band:#e4e4e4;
  --dark:#333333;
  --white:#ffffff;
  --line:#d6d6d6;
}
*{box-sizing:border-box;margin:0;padding:0}
html,body{width:782px;height:1200px;overflow:hidden}
body{position:relative;background:var(--page);font-family:"Source Sans 3",sans-serif;color:var(--ink)}
.abs{position:absolute}
.promo-strip{left:0;top:0;width:782px;height:26px;background:var(--band);font-size:8px;line-height:26px;text-align:center;color:var(--ink)}
.utility-bar{left:0;top:26px;width:782px;height:26px;background:var(--dark);color:#ddd;font-size:8px;line-height:26px}
.utility-bar .tagline{position:absolute;left:86px;color:#bbb}
.utility-bar .links{position:absolute;right:92px;display:flex;gap:6px;color:var(--white);font-weight:600;font-size:7px;align-items:center}
.utility-bar .sep{color:#aaa}
.site-header{left:0;top:52px;width:782px;height:115px;background:var(--white)}
.brand{position:absolute;left:86px;top:22px;width:110px;text-align:center}
.brand .monogram{display:block;width:30px;height:30px;margin:0 auto 4px;border:1px solid var(--gold)}
.brand .name{font-size:13px;letter-spacing:5px;color:var(--gold);font-weight:400}
.brand .motto{font-size:6px;font-style:italic;color:var(--ink);margin-top:3px}
.main-nav{position:absolute;top:50px;left:457px;display:flex;gap:0;font-size:10px;color:var(--ink)}
.main-nav span{position:absolute;white-space:nowrap}
.hero{left:86px;top:188px;width:609px;height:260px;background:radial-gradient(circle at 80% 40%,#e9c9a6 0%,#d9a970 35%,#f3ddb4 70%,#e8b775 100%)}
.hero-title{left:148px;top:285px;font-size:26px;font-weight:600;color:var(--gold-dark)}
.hero-cta{left:148px;top:319px;width:78px;height:25px;background:var(--white);font-size:9.5px;line-height:25px;text-align:center;color:var(--ink);letter-spacing:.3px}
.hero-arrow{width:24px;height:24px;border-radius:50%;background:rgba(255,255,255,.75);top:306px}
.dots{left:370px;top:459px;display:flex;gap:10px}
.dots i{display:block;width:6px;height:6px;border-radius:50%;background:#777}
.dots i.on{background:var(--gold)}
.offer{top:486px;width:194px;height:125px;color:var(--white);text-align:center}
.offer .fill{position:absolute;inset:0}
.offer .top{position:absolute;top:18px;width:100%;font-size:11px}
.offer .rule{position:absolute;left:14px;right:14px;height:1px;background:rgba(255,255,255,.8)}
.offer .big{position:absolute;top:50px;width:100%;font-size:21px;font-weight:600;letter-spacing:.5px}
.offer .bottom{position:absolute;top:94px;width:100%;font-size:11px}
.filter{top:647px;width:109px}
.filter label{display:block;font-size:9px;color:var(--ink);margin-bottom:5px}
.filter .select{height:25px;background:var(--white);border:1px solid var(--line);font-size:7.5px;color:#666;line-height:23px;padding-left:9px;position:relative}
.filter .select svg{position:absolute;right:8px;top:9px}
.divider{left:86px;top:708px;width:609px;height:1px;background:var(--line)}
.section-title{left:86px;top:730px;font-size:15px;font-weight:600;color:var(--gold)}
.sort{left:594px;top:734px;font-size:8.5px;color:var(--ink)}
.card{top:767px;width:141px;height:208px;background:var(--white);border:1px solid var(--line)}
.card .photo{position:absolute;left:2px;top:2px;right:2px;height:104px;background:radial-gradient(circle at 50% 50%,#e2e2e2 0%,#f6f6f6 55%,#f8f8f8 100%)}
.card .title{position:absolute;left:5px;top:117px;width:130px;font-size:8px;line-height:11px;color:var(--gold)}
.card .price{position:absolute;left:5px;top:145px;font-size:7px;color:var(--ink)}
.card .heart{position:absolute;left:6px;top:162px}
.card .btn{position:absolute;top:181px;width:67px;height:23px;border:1px solid var(--line);font-size:6.5px;color:#666;line-height:21px;text-align:center}
.side-arrow{top:862px}
.site-footer{left:0;top:1028px;width:782px;height:172px;background:var(--dark);color:var(--white)}
.col{position:absolute;top:30px}
.col h4{font-size:10px;font-weight:600;margin-bottom:7px}
.col li{list-style:none;font-size:6.5px;color:#ccc;line-height:14.5px}
.col li::before{content:"• ";color:#aaa}
.col.social li::before{content:none}
.col.social li{display:flex;align-items:center;gap:6px;line-height:19.5px}
.col.social li i{display:block;width:6px;height:6px;border-radius:50%;background:#ccc}
.newsletter{position:absolute;left:539px;top:48px;width:156px;height:26px;background:var(--white);font-size:6.5px;color:var(--ink);line-height:26px;padding-left:11px}
.newsletter svg{position:absolute;right:9px;top:8px}
.footer-rule{position:absolute;left:86px;top:128px;width:609px;height:1px;background:#555}
.copyright{position:absolute;left:0;width:782px;top:145px;text-align:center;font-size:7.5px;color:#ccc}
</style>
</head>
<body>
<div class="abs promo-strip">Free shipping on all orders over $500</div>
<div class="abs utility-bar">
  <span class="tagline">Vestibulum condimentum</span>
  <div class="links"><span>Currency : HKD ⌄</span><span class="sep">|</span><span>Sign-in</span><span class="sep">|</span><span>Wishlist</span><span class="sep">|</span><span>My Account</span><span class="sep">|</span><span>Cart - 0 items</span>
    <svg width="8" height="7" viewBox="0 0 8 7"><path d="M0 0h1.5l1 4h4.5l1-3H2" fill="none" stroke="#fff" stroke-width="1"/><circle cx="3" cy="6" r=".8" fill="#fff"/><circle cx="6.5" cy="6" r=".8" fill="#fff"/></svg>
    <span class="sep">|</span>
    <svg width="8" height="8" viewBox="0 0 8 8"><circle cx="3.3" cy="3.3" r="2.5" fill="none" stroke="#fff" stroke-width="1.2"/><path d="M5.2 5.2L7.5 7.5" stroke="#fff" stroke-width="1.4"/></svg>
  </div>
</div>
<header class="abs site-header">
  <div class="brand">
    <span class="monogram"></span>
    <div class="name">VELISTO</div>
    <div class="motto">Jewellery you'll fall in love with...</div>
  </div>
  <nav class="main-nav">
    <span style="left:0;color:var(--gold)">Home</span>
    <span style="left:50px">Shop</span>
    <span style="left:97px">Blog</span>
    <span style="left:141px">About us</span>
    <span style="left:204px">Contact</span>
  </nav>
</header>

<div class="abs hero" role="img" aria-label="Woman wearing a diamond drop earring and a sapphire ring against warm golden bokeh lights"></div>
<div class="abs hero-title">We celebrate women here!</div>
<div class="abs hero-cta">SHOP NOW</div>
<svg class="abs hero-arrow" style="left:101px" viewBox="0 0 24 24"><path d="M14 7l-5 5 5 5" fill="none" stroke="#b08a55" stroke-width="2"/></svg>
<svg class="abs hero-arrow" style="left:656px" viewBox="0 0 24 24"><path d="M10 7l5 5-5 5" fill="none" stroke="#b08a55" stroke-width="2"/></svg>
<div class="abs dots"><i class="on"></i><i></i><i></i></div>

<div class="abs offer" style="left:86px">
  <div class="fill" role="img" aria-label="Diamond ring close-up in grey tones" style="background:linear-gradient(135deg,#8a8a8a,#6e6e6e 50%,#9a9a9a)"></div>
  <div class="top">EXTRA 10% OFF</div><div class="rule" style="top:43px"></div>
  <div class="big">DIAMOND RINGS</div><div class="rule" style="top:80px"></div>
  <div class="bottom">TILL MARCH 31ST, 2018</div>
</div>
<div class="abs offer" style="left:294px">
  <div class="fill" role="img" aria-label="Ornate gold chain pattern in grey tones" style="background:linear-gradient(135deg,#5e5e5e,#7a7a7a 50%,#555)"></div>
  <div class="top">3 DAYS</div><div class="rule" style="top:43px"></div>
  <div class="big">GOLD</div><div class="rule" style="top:80px"></div>
  <div class="bottom">25% OFFER</div>
</div>
<div class="abs offer" style="left:502px">
  <div class="fill" role="img" aria-label="Large ruby ring in grey tones" style="background:linear-gradient(135deg,#2c2c2c,#555 45%,#333)"></div>
  <div class="top">NEW</div><div class="rule" style="top:43px"></div>
  <div class="big">RUBY</div><div class="rule" style="top:80px"></div>
  <div class="bottom">ARRIVAL</div>
</div>

<div class="abs filter" style="left:86px"><label>Type</label><div class="select">Rings<svg width="6" height="4" viewBox="0 0 6 4"><path d="M0 0l3 3 3-3" fill="none" stroke="#666"/></svg></div></div>
<div class="abs filter" style="left:211px"><label>Collection</label><div class="select">Select<svg width="6" height="4" viewBox="0 0 6 4"><path d="M0 0l3 3 3-3" fill="none" stroke="#666"/></svg></div></div>
<div class="abs filter" style="left:336px"><label>Metal</label><div class="select">10K Rose Gold<svg width="6" height="4" viewBox="0 0 6 4"><path d="M0 0l3 3 3-3" fill="none" stroke="#666"/></svg></div></div>
<div class="abs filter" style="left:461px"><label>Gemstone</label><div class="select">Amethyst<svg width="6" height="4" viewBox="0 0 6 4"><path d="M0 0l3 3 3-3" fill="none" stroke="#666"/></svg></div></div>
<div class="abs filter" style="left:586px"><label>Price range</label><div class="select">Select<svg width="6" height="4" viewBox="0 0 6 4"><path d="M0 0l3 3 3-3" fill="none" stroke="#666"/></svg></div></div>

<div class="abs divider"></div>
<div class="abs section-title">Our Products</div>
<div class="abs sort">Sort by : Our Favourites ⌄</div>

<svg class="abs side-arrow" style="left:30px" width="10" height="16" viewBox="0 0 10 16"><path d="M8 1L2 8l6 7" fill="none" stroke="#777" stroke-width="1.5"/></svg>
<svg class="abs side-arrow" style="left:741px" width="10" height="16" viewBox="0 0 10 16"><path d="M2 1l6 7-6 7" fill="none" stroke="#777" stroke-width="1.5"/></svg>

<div class="abs card" style="left:86px">
  <div class="photo" role="img" aria-label="Silver solitaire diamond ring"></div>
  <div class="title">Fusce sollicitudin lorem et luctus volutpat</div>
  <div class="price">3908 HKD</div>
  <svg class="heart" width="9" height="8" viewBox="0 0 10 9"><path d="M5 8.5L1 4.5A2.3 2.3 0 015 1.5a2.3 2.3 0 014 3z" fill="none" stroke="#555"/></svg>
  <div class="btn" style="left:3px">ADD TO CART</div><div class="btn" style="left:72px">QUICK VIEW</div>
</div>
<div class="abs card" style="left:242px">
  <div class="photo" role="img" aria-label="Diamond halo engagement ring"></div>
  <div class="title">Proin placerat dapibus gravida</div>
  <div class="price">4103 HKD</div>
  <svg class="heart" width="9" height="8" viewBox="0 0 10 9"><path d="M5 8.5L1 4.5A2.3 2.3 0 015 1.5a2.3 2.3 0 014 3z" fill="none" stroke="#555"/></svg>
  <div class="btn" style="left:3px">ADD TO CART</div><div class="btn" style="left:72px">QUICK VIEW</div>
</div>
<div class="abs card" style="left:398px">
  <div class="photo" role="img" aria-label="Princess cut diamond ring with pavé band"></div>
  <div class="title">Aenean facilisis tincidunt lectus, id dictum nisi</div>
  <div class="price">4571 HKD</div>
  <svg class="heart" width="9" height="8" viewBox="0 0 10 9"><path d="M5 8.5L1 4.5A2.3 2.3 0 015 1.5a2.3 2.3 0 014 3z" fill="none" stroke="#555"/></svg>
  <div class="btn" style="left:3px">ADD TO CART</div><div class="btn" style="left:72px">QUICK VIEW</div>
</div>
<div class="abs card" style="left:554px">
  <div class="photo" role="img" aria-label="Twisted band diamond ring"></div>
  <div class="title">Vivamus efficitur ex condimen-tum, malesuada eros</div>
  <div class="price">2742 HKD</div>
  <svg class="heart" width="9" height="8" viewBox="0 0 10 9"><path d="M5 8.5L1 4.5A2.3 2.3 0 015 1.5a2.3 2.3 0 014 3z" fill="none" stroke="#555"/></svg>
  <div class="btn" style="left:3px">ADD TO CART</div><div class="btn" style="left:72px">QUICK VIEW</div>
</div>

<footer class="abs site-footer">
  <div class="col" style="left:86px"><h4>About Us</h4><ul><li>Our Story</li><li>Wholesale inquiries</li></ul></div>
  <div class="col" style="left:200px"><h4>Shopping</h4><ul><li>Orders</li><li>Wishlist</li><li>Size Guide</li></ul></div>
  <div class="col" style="left:294px"><h4>Customer Care</h4><ul><li>Returns</li><li>FAQ</li><li>Care &amp; Warrenty</li><li>Contact Us</li></ul></div>
  <div class="col social" style="left:425px"><h4>Follow us on</h4><ul><li><i></i>Friendly</li><li><i></i>Snapgram</li><li><i></i>Pinboard</li></ul></div>
  <div class="col" style="left:539px"><h4>Sign-up to the Newsletter</h4></div>
  <div class="newsletter">Email Address
    <svg width="11" height="9" viewBox="0 0 11 9"><rect width="11" height="9" rx="1" fill="#333"/><path d="M0.5 1l5 4 5-4" fill="none" stroke="#fff" stroke-width="1"/></svg>
  </div>
  <div class="footer-rule"></div>
  <div class="copyright">Copyright © 2017 Velisto Jewellery.&nbsp;&nbsp; All rights reserved.</div>
</footer>
</body>
</html>
```